Stylish Business Cards Wanted

- DOUBLE SIDED Design Required -

High end, edgy cards for a corporate and personal stylist. Must include logo,
Name: Belinda Harwick
Title: Director and Stylist
telephone : +61 8 7142 5809
email: belinda@theloombriefing.example
website: theloombriefing.example
Tag: Corporate Workwear & Uniform Specialist | Personal Stylist
Would like nice icons for telephone, email, website

Target Market(s)

Businesses wanting stylish uniforms, people wanting stylish wardrobes

Industry/Entity Type

Corporate Workwear Stylist

Contact Information for Business Card

I would like black, white and gold foiling incorporated in the design - possibly a touch of the other colours on my branding guide attached Name: Belinda Harwick Title: Director and Stylist telephone : +61 8 7142 5809 email: belinda@theloombriefing.example website: theloombriefing.example Tag: Corporate Workwear & Uniform Specialist | Personal Stylist Would like nice icons for telephone, email, website

Font styles to use
Other font styles liked:
• Raleway

Colors

Designer to choose colors to be used in the design.

Requirements
Must have
• Gold foil accents

```html
<!DOCTYPE html>
<html lang="en">
<head>
<meta charset="utf-8">
<title>The Loom Briefing — Business Cards</title>
<link rel="stylesheet" href="https://fonts.googleapis.com/css2?family=Raleway:wght@400;500;600&display=swap">
<style>
  :root {
    --backdrop: #ebebeb;
    --card-white: #ffffff;
    --card-black: #231f20;
    --gold: #e2b94c;
    --ink: #1e1b1c;
    --silver: #a7a7a9;
    --light-text: #d8d8d8;
    --font: "Raleway", sans-serif;
  }
  * { box-sizing: border-box; margin: 0; padding: 0; }
  html, body {
    width: 1200px; height: 507px; overflow: hidden;
    background: var(--backdrop);
    font-family: var(--font);
  }
  .canvas { position: relative; width: 1200px; height: 507px; }

  .card {
    position: absolute; top: 106px;
    width: 493px; height: 295px;
    box-shadow: 0 10px 22px rgba(0,0,0,0.18);
  }
  .card--front { left: 83px; background: var(--card-white); }
  .card--back  { left: 624px; background: var(--card-black); }

  .card__frame {
    position: absolute; left: 26px; top: 26px; right: 26px; bottom: 26px;
    border: 1px solid var(--gold);
  }

  /* Front */
  .brand-name {
    position: absolute; left: 0; right: 0;
    text-align: center; font-weight: 600; letter-spacing: 1px;
  }
  .card--front .brand-name { top: 110px; font-size: 34px; color: var(--ink); }
  .tagline {
    position: absolute; left: 0; right: 0; top: 206px;
    text-align: center; font-size: 14.5px; color: var(--ink);
  }
  .tagline__divider { color: var(--gold); margin: 0 5px; }

  /* Back */
  .card--back .brand-name {
    left: 26px; right: auto; width: 170px; top: 120px;
    font-size: 25px; line-height: 1.15; color: var(--silver);
  }
  .divider {
    position: absolute; left: 197px; top: 93px;
    width: 1px; height: 109px; background: #6d6a6b;
  }
  .contact { position: absolute; left: 210px; top: 92px; }
  .contact__name { font-size: 22px; color: var(--gold); font-weight: 400; line-height: 1.2; }
  .contact__title { font-size: 11px; color: var(--light-text); margin-top: 1px; }
  .contact__list { list-style: none; margin-top: 6px; }
  .contact__item {
    display: flex; align-items: center; gap: 7px;
    font-size: 14px; color: var(--light-text); height: 21.5px;
  }
  .contact__icon { width: 11px; height: 11px; flex: none; }
</style>
</head>
<body>
<div class="canvas">

  <section class="card card--front" aria-label="Card front">
    <div class="card__frame"></div>
    <p class="brand-name">The Loom Briefing</p>
    <p class="tagline">Corporate Workwear<span class="tagline__divider">|</span>Uniform Specialist<span class="tagline__divider">|</span>Personal Stylist</p>
  </section>

  <section class="card card--back" aria-label="Card back">
    <div class="card__frame"></div>
    <p class="brand-name">The Loom<br>Briefing</p>
    <div class="divider"></div>
    <div class="contact">
      <h1 class="contact__name">Belinda Harwick</h1>
      <p class="contact__title">Director and Stylist</p>
      <ul class="contact__list">
        <li class="contact__item">
          <svg class="contact__icon" viewBox="0 0 12 12" aria-hidden="true">
            <circle cx="6" cy="6" r="6" fill="var(--gold)"/>
            <path d="M3 5.2c0-1 1.3-1.6 3-1.6s3 .6 3 1.6l-1.2.3-.3-.8H4.5l-.3.8z M4.2 6h3.6l.6 2.2H3.6z" fill="var(--card-black)"/>
          </svg>
          +61 8 7142 5809
        </li>
        <li class="contact__item">
          <svg class="contact__icon" viewBox="0 0 12 12" aria-hidden="true">
            <circle cx="6" cy="6" r="6" fill="var(--gold)"/>
            <rect x="3" y="4" width="6" height="4.2" fill="var(--card-black)"/>
            <path d="M3 4l3 2.3L9 4" stroke="var(--gold)" stroke-width=".8" fill="none"/>
          </svg>
          belinda@theloombriefing.example
        </li>
        <li class="contact__item">
          <svg class="contact__icon" viewBox="0 0 12 12" aria-hidden="true">
            <circle cx="6" cy="6" r="6" fill="var(--gold)"/>
            <g stroke="var(--card-black)" stroke-width=".8" fill="none">
              <circle cx="6" cy="6" r="3.3"/>
              <ellipse cx="6" cy="6" rx="1.4" ry="3.3"/>
              <path d="M2.7 6h6.6M3.2 4.4h5.6M3.2 7.6h5.6"/>
            </g>
          </svg>
          theloombriefing.example
        </li>
      </ul>
    </div>
  </section>

</div>
</body>
</html>
```